NEW Modern Sleek Business Card for VR Language Startup

Our startup is using VR to lead the next wave of world language education. We need a two-sided business card that introduces the larger organization (Brightloom Language Inc) and our contact info on one side and shows the product, Glimwoorld, on the other side.

Side 1 (contact info)= Brightloom Logo and Contact info (name, title, phone, email)

Side 2 (product)= Glimworld logo, text, and website
Text= Culturally Immersive Language Learning Games
Website= www.glimworld-play.com

Target Market(s)

Education, Technology

Contact Information for Business Card

Contact info will be updated upon approval of the design. For now, put this as a placeholder.

Perry Dunmore
Founder & CEO
pdunmore@quillpost-mail.net
(555)-014-2286

Font styles to use
Other font styles liked:
• Gibson and Century Gothic are the brand fonts

Requirements
Nice to have
• I would love to see cohesion between the design and colors of the two logos. I have attached a few business card designs that I like, so you can get a feel for my preferred style.

```html
<!DOCTYPE html>
<html lang="en">
<head>
<meta charset="utf-8">
<title>Brightloom Language — Business Card</title>
<link href="https://fonts.googleapis.com/css2?family=Montserrat:wght@600;700&family=Questrial&display=swap" rel="stylesheet">
<style>
  :root {
    --stage: #d9d9db;
    --card: #1c1c1d;
    --card-back: #121213;
    --white: #ffffff;
    --muted: #5f5f62;
    --violet: #6b5cf6;
    --cyan: #22d3ee;
    --blue: #3b9cf5;
    --orange: #f7a93a;
    --red: #ff3344;
    --magenta: #c94aa0;
  }
  * { box-sizing: border-box; margin: 0; padding: 0; }
  html, body { width: 1200px; height: 1200px; overflow: hidden; }
  body {
    background: var(--stage);
    font-family: "Questrial", "Century Gothic", sans-serif;
    display: flex; flex-direction: column; align-items: center; justify-content: center;
    gap: 60px;
  }
  .card {
    position: relative;
    width: 900px; height: 514px;
    border-radius: 34px;
    overflow: hidden;
    box-shadow: 0 18px 40px rgba(0,0,0,0.25);
  }

  /* Product side */
  .card--product {
    background: var(--card-back);
    display: flex; flex-direction: column; align-items: center; justify-content: center;
  }
  .product-mark { display: flex; align-items: center; gap: 18px; }
  .product-mark__dot {
    width: 54px; height: 54px; border-radius: 50%;
    background: linear-gradient(160deg, var(--cyan), var(--violet));
  }
  .product-mark__name {
    font-size: 64px; color: var(--muted); letter-spacing: 1px;
  }
  .product-tagline {
    margin-top: 14px; font-size: 22px; color: var(--muted); letter-spacing: 1px;
  }
  .product-url {
    margin-top: 60px; font-family: "Montserrat", sans-serif; font-weight: 700;
    font-size: 22px; color: var(--violet); letter-spacing: 0.5px;
  }

  /* Contact side */
  .card--contact { background: var(--card); }
  .brand-art {
    position: absolute; left: 0; top: 0; bottom: 0; width: 400px;
    background: linear-gradient(200deg, var(--orange) 0%, var(--red) 35%, var(--magenta) 58%, var(--violet) 76%, var(--blue) 100%);
    border-radius: 0 60% 40% 0 / 0 45% 30% 0;
  }
  .contact {
    position: absolute; right: 70px; top: 70px;
    display: flex; flex-direction: column; align-items: flex-end; text-align: right;
  }
  .company { display: flex; align-items: center; gap: 14px; }
  .company__dot {
    width: 28px; height: 28px; border-radius: 50%;
    background: linear-gradient(160deg, var(--red), var(--violet));
  }
  .company__name {
    font-family: "Montserrat", sans-serif; font-weight: 700;
    font-size: 46px; color: var(--white); letter-spacing: 8px;
  }
  .company__sub {
    margin-top: 6px; font-size: 20px; color: var(--white); letter-spacing: 16px;
    margin-right: -16px;
  }
  .person {
    margin-top: 60px; font-family: "Montserrat", sans-serif; font-weight: 700;
    font-size: 32px; color: var(--white); letter-spacing: 0.5px;
  }
  .role { margin-top: 4px; font-size: 20px; color: var(--white); }
  .detail {
    margin-top: 14px; display: flex; align-items: center; gap: 12px;
    font-size: 20px; color: var(--white);
  }
  .detail + .detail { margin-top: 8px; }
  .detail svg { width: 20px; height: 20px; }
</style>
</head>
<body>

  <section class="card card--product" aria-label="Product side">
    <div class="product-mark">
      <span class="product-mark__dot"></span>
      <span class="product-mark__name">Glimworld</span>
    </div>
    <p class="product-tagline">Culturally Immersive Language Learning Games</p>
    <p class="product-url">www.glimworld-play.com</p>
  </section>

  <section class="card card--contact" aria-label="Contact side">
    <div class="brand-art" role="img" aria-label="Large gradient brand graphic in orange, red, violet and blue"></div>
    <div class="contact">
      <div class="company">
        <span class="company__dot"></span>
        <span class="company__name">BRIGHTLOOM</span>
      </div>
      <p class="company__sub">LANGUAGE</p>
      <p class="person">PERRY DUNMORE</p>
      <p class="role">President</p>
      <p class="detail">pdunmore@quillpost-mail.net
        <svg viewBox="0 0 20 20" aria-hidden="true"><rect x="2" y="5" width="16" height="11" rx="1.5" fill="none" stroke="var(--cyan)" stroke-width="1.8"/><path d="M2.5 5.5 L10 11 L17.5 5.5" fill="none" stroke="var(--cyan)" stroke-width="1.8"/></svg>
      </p>
      <p class="detail">(555)-014-2286
        <svg viewBox="0 0 20 20" aria-hidden="true"><circle cx="10" cy="10" r="8" fill="none" stroke="var(--cyan)" stroke-width="1.6"/><ellipse cx="10" cy="10" rx="3.5" ry="8" fill="none" stroke="var(--cyan)" stroke-width="1.4"/><path d="M2 10 H18 M3.5 6 H16.5 M3.5 14 H16.5" stroke="var(--cyan)" stroke-width="1.2"/></svg>
      </p>
    </div>
  </section>

</body>
</html>
```